Bright Harbor website redesign

We need a redesign for a website: mybrightharbor.example.

I already created a video going over what exactly is needed in the design.

See Video here: https://files.example.net/file/d/7xQpL2mR9vTz4KwB8nYcH3jDs6FgA1eU0/view?usp=sharing

Searchly Slide shown in Video: https://slides.example.net/presentation/d/9KP_Rtnwq3XbzmLeYc7VhJ2GoUd4Fs_PaiTe6q1kQ5Wr/edit?usp=sharing

Holidays in India so we did not get enough design entries or quality.

Target Market(s)

Dentistry

Industry/Entity Type

Dentistry

Number of Pages Required

1 page

Colors
0094D4
00A9DD
6FCCEA
C7EBF8
E9F6FB
00AB8E
00BBA5
67D7C9
C6EFE9
E9F9F6

Requirements
Must have
• See 13 min video link in description - shows what to do.

```html
<!DOCTYPE html>
<html lang="en">
<head>
<meta charset="utf-8">
<title>Bright Harbor – Family &amp; Cosmetic Dentistry</title>
<link href="https://fonts.googleapis.com/css2?family=Raleway:wght@300;400;600;700;800&family=Lato:wght@400;700&display=swap" rel="stylesheet">
<style>
:root{
  --blue:#2b95e0;
  --blue-deep:#1279c4;
  --blue-pale:#eaf5fc;
  --navy:#2f4f63;
  --slate:#2f5a6e;
  --green:#6aab2f;
  --green-dark:#5a9a25;
  --red:#d9262b;
  --text:#4a5560;
  --muted:#8a95a0;
  --line:#c8dcea;
  --white:#fff;
}
*{box-sizing:border-box;margin:0;padding:0}
html,body{width:1200px;height:4199px;overflow:hidden}
body{font-family:"Lato",sans-serif;color:var(--text);background:var(--white);position:relative}
.abs{position:absolute}
h1,h2,h3,.heading{font-family:"Raleway",sans-serif}

/* header */
.site-header{position:absolute;left:0;top:0;width:1200px;height:105px;background:var(--white)}
.brand{left:90px;top:22px;display:flex;align-items:center;gap:10px}
.brand-dot{width:22px;height:22px;border-radius:50%;background:var(--green)}
.brand-name{font-family:"Raleway",sans-serif;font-weight:700;font-size:28px;color:var(--green)}
.phone{left:640px;top:16px;display:flex;align-items:center;gap:8px;font-family:"Raleway",sans-serif;font-weight:700;font-size:16px;color:var(--navy)}
.phone-icon{width:22px;height:22px;border-radius:50%;background:var(--red);display:flex;align-items:center;justify-content:center}
.pill{display:flex;align-items:center;justify-content:center;border-radius:20px;color:#fff;font-family:"Raleway",sans-serif;font-weight:700;font-size:12px;height:34px}
.btn-schedule{left:815px;top:8px;width:145px;background:var(--green)}
.btn-emergency{left:967px;top:8px;width:144px;background:var(--blue)}
.main-nav{left:316px;top:68px;display:flex;gap:0;font-size:13px;color:var(--navy)}
.main-nav span{position:absolute;white-space:nowrap}
.nav-active{position:absolute;left:314px;top:101px;width:78px;height:4px;background:var(--green)}

/* hero */
.hero{top:105px;left:0;width:1200px;height:571px;background:var(--blue)}
.hero-title{left:105px;top:160px;color:#fff;font-size:40px;line-height:44px}
.hero-title .thin{font-weight:300;letter-spacing:1px}
.hero-title .bold{font-weight:700;letter-spacing:1px}
.hero-sub{left:108px;top:265px;color:#fff;font-family:"Raleway",sans-serif;font-weight:600;font-size:17px;letter-spacing:1.2px;line-height:23px}
.btn-green{background:var(--green);color:#fff;border-radius:28px;font-family:"Raleway",sans-serif;font-weight:700;font-size:13px;display:flex;align-items:center;justify-content:center}
.hero-btn{left:104px;top:332px;width:232px;height:52px}
.hero-art{left:530px;top:75px;width:635px;height:470px;border-radius:40px;background:linear-gradient(135deg,#1f5f95 0%,#2a78b8 60%,#2b95e0 100%);opacity:.55}

/* section titles */
.section-title{width:1200px;left:0;text-align:center;font-size:30px;color:var(--navy);letter-spacing:1px}
.section-title .thin{font-weight:400}
.section-title .bold{font-weight:700}
.title-rule{width:50px;height:3px;background:var(--green);left:575px}

/* team */
.member{width:300px;text-align:center}
.member-photo{width:285px;height:285px;border-radius:50%;margin:0 auto;background:radial-gradient(circle at 50% 40%,#e9e6e2 0%,#cfd4d8 70%,#bfc6cc 100%)}
.member-photo.active{border:6px solid var(--blue);box-shadow:inset 0 0 0 4px #fff;background:radial-gradient(circle at 50% 40%,#eeeeee 0%,#d6dbe0 70%,#c4cbd1 100%)}
.member-name{margin-top:26px;font-family:"Raleway",sans-serif;font-weight:700;font-size:19px;color:var(--navy)}
.member-role{margin-top:8px;font-size:16px;color:var(--green);font-weight:700}

/* bio */
.bio{top:1270px;left:0;width:1200px;height:440px;background:var(--blue-pale)}
.bio-pointer{left:582px;top:1252px;width:0;height:0;border-left:18px solid transparent;border-right:18px solid transparent;border-bottom:18px solid var(--blue-pale)}
.bio-text{left:175px;top:74px;width:860px;text-align:center;font-size:14.5px;line-height:27px;color:var(--text)}
.bio-members{left:0;top:209px;width:1200px;text-align:center;font-size:14.5px}
.org-row{left:187px;top:262px;display:flex;gap:5px}
.org{width:206px;height:76px;border:2px solid var(--line);background:#f5fafd;display:flex;align-items:center;justify-content:center;text-align:center;font-size:13px;line-height:19px;color:var(--navy);padding:0 14px}

/* services */
.service{width:240px;text-align:center}
.service-icon{width:108px;height:108px;border-radius:50%;margin:0 auto;border:2px solid #cfe5f5;background:#fff;box-shadow:0 4px 10px rgba(43,149,224,.12);display:flex;align-items:center;justify-content:center}
.service-icon.active{background:var(--blue);border:6px solid #fff;box-shadow:0 0 0 2px var(--blue)}
.service-label{margin-top:26px;font-family:"Raleway",sans-serif;font-weight:700;font-size:14.5px;color:var(--navy);letter-spacing:.3px}

/* difference */
.difference{top:2560px;left:0;width:1200px;height:665px;background:var(--slate)}
.diff-frame{left:112px;top:65px;width:750px;height:512px;border:4px solid var(--green)}
.diff-title{left:162px;top:115px;color:#fff;font-size:26px;line-height:29px;letter-spacing:1px}
.diff-title .thin{font-weight:400}
.diff-title .bold{font-weight:700}
.diff-body{left:163px;top:205px;width:565px;color:#e4edf2;font-size:12px;line-height:17px}
.diff-body p{margin-bottom:16px}
.review-card{left:773px;top:95px;width:305px;height:440px;background:#f3f4f5}
.rc-head{text-align:center;padding-top:16px;font-family:"Raleway",sans-serif;font-weight:700;font-size:13px;color:var(--navy)}
.stars{color:#f5b324;letter-spacing:3px;font-size:17px}
.rc-platforms{position:absolute;left:63px;top:108px;width:190px;height:38px;background:#fff;display:flex;justify-content:space-around;align-items:center;font-size:11px;font-weight:700;color:var(--navy)}
.rc-inner{position:absolute;left:52px;top:156px;width:200px;height:262px;background:#fff;padding:14px 12px}
.rc-avatar{width:36px;height:36px;border-radius:50%;background:#c9b5a5}
.arrow{position:absolute;top:238px;color:var(--blue);font-size:22px;font-weight:700}

/* commit */
.commit{top:3225px;left:0;width:1200px;height:470px;background:linear-gradient(90deg,#2b95e0 0%,#0f7ac2 100%)}
.commit-frame{left:360px;top:70px;width:680px;height:300px;border:3px solid rgba(255,255,255,.35)}
.commit-photo{left:140px;top:70px;width:320px;height:320px;border-radius:50%;border:12px solid #fff;background:linear-gradient(150deg,#e8d8cc 0%,#cfd9e2 55%,#a9c4d9 100%)}
.commit-title{left:516px;top:108px;color:#fff;font-size:27px;line-height:36px;letter-spacing:1.2px}
.commit-title .bold{font-weight:700}
.commit-title .thin{font-weight:400}
.commit-rule{left:516px;top:190px;width:48px;height:2px;background:rgba(255,255,255,.8)}
.commit-sub{left:518px;top:216px;color:#fff;font-size:19px;letter-spacing:.5px}
.commit-btn{left:512px;top:275px;width:226px;height:48px}

/* footer */
.footer{top:3695px;left:0;width:1200px;height:380px;background:#fff}
.f-heading{font-family:"Raleway",sans-serif;font-weight:700;font-size:17px;color:var(--navy);letter-spacing:.5px}
.f-rule{width:64px;height:2px;background:var(--blue);margin-top:8px}
.f-row{display:flex;gap:12px;font-size:13px;line-height:19px;color:var(--navy);margin-top:16px}
.hours{font-size:13px;color:var(--navy);line-height:29px}
.hours td{padding-right:0}
.hours td:first-child{width:115px}
.btn-red{background:var(--red);color:#fff;border-radius:20px;font-family:"Raleway",sans-serif;font-weight:700;font-size:12px;display:flex;align-items:center;justify-content:center}
.map{left:754px;top:120px;width:308px;height:185px;border:2px solid #d7dde2;background:linear-gradient(135deg,#f2f2ef 0%,#e6e8e6 100%)}
.bottom-bar{top:4075px;left:0;width:1200px;height:124px;border-top:1px solid #e3e7ea}
.bottom-nav{left:131px;top:30px;font-size:12px;color:var(--navy)}
.bottom-nav span{position:absolute;white-space:nowrap}
.copyright{left:131px;top:64px;font-size:10px;color:var(--navy);white-space:nowrap}
.socials{left:922px;top:25px;display:flex;gap:6px}
.socials span{width:24px;height:24px;border-radius:50%;background:var(--green)}
</style>
</head>
<body>

<header class="site-header">
  <div class="abs brand"><span class="brand-dot"></span><span class="brand-name">Bright Harbor</span></div>
  <div class="abs phone">
    <span class="phone-icon"><svg width="12" height="12" viewBox="0 0 24 24"><path fill="#fff" d="M6.6 10.8a15.1 15.1 0 006.6 6.6l2.2-2.2c.3-.3.7-.4 1-.2 1.1.4 2.3.6 3.6.6.6 0 1 .4 1 1V20c0 .6-.4 1-1 1C10.6 21 3 13.4 3 4c0-.6.4-1 1-1h3.5c.6 0 1 .4 1 1 0 1.3.2 2.5.6 3.6.1.3 0 .7-.2 1z"/></svg></span>
    (555) 014-2290
  </div>
  <div class="abs pill btn-schedule">Schedule Online</div>
  <div class="abs pill btn-emergency">Emergency</div>
  <nav class="abs main-nav" style="left:0;top:68px;width:1200px;height:20px">
    <span style="left:316px">About Us ▾</span>
    <span style="left:413px">Services ▾</span>
    <span style="left:505px">Financing</span>
    <span style="left:606px">Testimonials</span>
    <span style="left:722px">New Patient Visit</span>
    <span style="left:869px">Specials</span>
    <span style="left:961px">Contact Us</span>
    <span style="left:1069px">Blog</span>
  </nav>
  <div class="nav-active"></div>
</header>

<section class="abs hero">
  <h1 class="abs hero-title"><span class="thin">CREATING</span><br><span class="bold">HEALTHIER SMILES</span></h1>
  <p class="abs hero-sub">WITH ADVANCED TECHNOLOGY AND<br>AFFORDABLE TREATMENT</p>
  <div class="abs btn-green hero-btn">BOOK AN APPOINTMENT</div>
  <div class="abs hero-art" role="img" aria-label="Illustration of large teeth with dental mirror and tools"></div>
</section>

<section class="abs" style="top:676px;left:0;width:1200px;height:594px">
  <h2 class="abs section-title" style="top:62px"><span class="thin">MEET </span><span class="bold">OUR TEAM</span></h2>
  <div class="abs title-rule" style="top:115px"></div>
  <div class="abs member" style="left:140px;top:162px">
    <div class="member-photo" role="img" aria-label="Portrait of Dr. Arun Mehra"></div>
    <div class="member-name">Meet Dr. Arun Mehra</div>
    <div class="member-role">General Dentist</div>
  </div>
  <div class="abs member" style="left:450px;top:162px">
    <div class="member-photo active" role="img" aria-label="Portrait of Dr. Kavya Rao"></div>
    <div class="member-name">Dr. Kavya Rao</div>
    <div class="member-role">Endodontist</div>
  </div>
  <div class="abs member" style="left:770px;top:162px">
    <div class="member-photo" role="img" aria-label="Portrait of Dr. Nisha Desai"></div>
    <div class="member-name">Dr. Nisha Desai</div>
    <div class="member-role">Cosmetic Dentist</div>
  </div>
</section>

<div class="abs bio-pointer"></div>
<section class="abs bio">
  <p class="abs bio-text">Dr. Rao received her specialty training in Endodontics from Westbrook University. She graduated with a Master of Science in dentistry degree, in endodontics. She has practiced in Southern California for many years as a general dentist before specializing in endodontics and uses her experience to help her patients make the right decisions, regarding their treatment plans. She is gentle, compassionate and is committed to providing the optimum care for her patients.</p>
  <p class="abs bio-members">Dr. Rao is a member of several professional and service organizations, including:</p>
  <div class="abs org-row">
    <div class="org">National Dental<br>Council (NDC)</div>
    <div class="org">State Dental<br>Society (SDS)</div>
    <div class="org">Heritage Dental<br>Guild (HDG)</div>
    <div class="org">Lakemont County Dental<br>Society (LCDS)</div>
  </div>
</section>

<section class="abs" style="top:1710px;left:0;width:1200px;height:850px">
  <h2 class="abs section-title" style="top:48px"><span class="thin">OUR </span><span class="bold">SERVICES</span></h2>
  <div class="abs title-rule" style="top:100px"></div>

  <svg width="0" height="0" style="position:absolute">
    <defs>
      <symbol id="tooth" viewBox="0 0 48 48"><path d="M14 8c-5 0-8 4-8 10 0 5 2 8 3 12 1 5 2 12 5 12 3 0 3-8 6-12 1-1 3-1 4 0 3 4 3 12 6 12 3 0 4-7 5-12 1-4 3-7 3-12 0-6-3-10-8-10-4 0-6 2-8 2s-4-2-8-2z" fill="none" stroke="currentColor" stroke-width="2.2" stroke-linejoin="round"/></symbol>
    </defs>
  </svg>

  <div class="abs service" style="left:117px;top:165px"><div class="service-icon active"><svg width="46" height="46" style="color:#fff"><use href="#tooth"/></svg></div><div class="service-label">DENTAL IMPLANTS</div></div>
  <div class="abs service" style="left:367px;top:165px"><div class="service-icon"><svg width="46" height="46" style="color:var(--blue)"><use href="#tooth"/></svg></div><div class="service-label">COSMETIC DENTISTRY</div></div>
  <div class="abs service" style="left:597px;top:165px"><div class="service-icon"><svg width="46" height="46" style="color:var(--blue)"><use href="#tooth"/></svg></div><div class="service-label">BRACES</div></div>
  <div class="abs service" style="left:837px;top:165px"><div class="service-icon"><svg width="46" height="46" style="color:var(--blue)"><use href="#tooth"/></svg></div><div class="service-label">CROWNS</div></div>

  <div class="abs service" style="left:115px;top:380px"><div class="service-icon"><svg width="46" height="46" style="color:var(--blue)"><use href="#tooth"/></svg></div><div class="service-label">BRIDGE</div></div>
  <div class="abs service" style="left:363px;top:380px"><div class="service-icon"><svg width="46" height="46" style="color:var(--blue)"><use href="#tooth"/></svg></div><div class="service-label">EXTRACTIONS</div></div>
  <div class="abs service" style="left:593px;top:380px"><div class="service-icon"><svg width="46" height="46" style="color:var(--blue)"><use href="#tooth"/></svg></div><div class="service-label">GUM DISEASE</div></div>
  <div class="abs service" style="left:837px;top:380px"><div class="service-icon"><svg width="46" height="46" style="color:var(--blue)"><use href="#tooth"/></svg></div><div class="service-label">ROOT CANAL</div></div>

  <div class="abs service" style="left:119px;top:597px"><div class="service-icon"><svg width="46" height="46" style="color:var(--blue)"><use href="#tooth"/></svg></div><div class="service-label">DENTURES</div></div>
  <div class="abs service" style="left:361px;top:597px"><div class="service-icon"><svg width="46" height="46" style="color:var(--blue)"><use href="#tooth"/></svg></div><div class="service-label">EMERGENCY DENTISTRY</div></div>
  <div class="abs service" style="left:597px;top:597px"><div class="service-icon"><svg width="46" height="46" style="color:var(--blue)"><use href="#tooth"/></svg></div><div class="service-label">VENEERS</div></div>
  <div class="abs service" style="left:833px;top:597px"><div class="service-icon"><svg width="46" height="46" style="color:var(--blue)"><use href="#tooth"/></svg></div><div class="service-label">CLEARSTEP ALIGNERS</div></div>
</section>

<section class="abs difference">
  <div class="abs diff-frame"></div>
  <h2 class="abs diff-title"><span class="thin">EXPERIENCE THE BRIGHT</span><br><span class="bold">HARBOR DIFFERENCE</span></h2>
  <div class="abs diff-body">
    <p>Your smile is our #1 priority. At Bright Harbor, we provide affordable and expert dental solutions. Whether you are looking for a family dentist or have any emergency such as needing a root canal in Lakemont, we are here for you! We want to keep your teeth healthy inside and out. We don't just clean teeth and send you on your way, we want to get to know you.</p>
    <p>We accept most HMO and PPO insurances. We offer various financing options through CarePay Plus, LendWell and In-House Plans.</p>
    <p>To constantly strive to achieve the highest level of skills and modern techniques and equipment so we can provide our patients with the best that Dentistry has to offer at our dental office in Lakemont, CA.</p>
    <p>We provide patients with the best experience you can find in all of Southern California. We provide a comfortable and friendly atmosphere to shatter any fears you may have. We supply you with all the information on your dental health options so you can feel comfortable in the choices you make, whether it's a routine check-up or dental implants in Lakemont.</p>
    <p>We are available for Emergency and Walk-ins.</p>
  </div>
  <div class="abs review-card">
    <div class="rc-head">AVERAGE RATING</div>
    <div style="text-align:center;margin-top:4px"><span class="stars">★★★★★</span> <b style="font-size:14px;color:var(--navy)">4.9</b></div>
    <div style="text-align:center;font-size:11px;margin-top:8px;color:var(--navy)"><span style="display:inline-block;width:14px;height:14px;border-radius:50%;background:var(--blue);vertical-align:middle"></span> 126 Reviews</div>
    <div class="rc-platforms"><span>Searchly</span><span>Reviewly</span><span>Friendbook</span></div>
    <span class="arrow" style="left:30px">‹</span>
    <span class="arrow" style="right:18px">›</span>
    <div class="rc-inner">
      <div class="stars" style="font-size:13px;text-align:center;padding-left:20px">★★★★★</div>
      <div style="display:flex;align-items:center;gap:8px;margin-top:2px">
        <div class="rc-avatar"></div><b style="font-size:13px;color:var(--navy)">Dana Whitfield</b>
      </div>
      <p style="font-size:9px;line-height:11px;margin-top:12px;color:var(--navy)">Dr. Mehra and her staff are awesome! Everyone is so nice and pleasant. I always have a great experience! I don't ever feel rushed and time is taken to answer questions and make sure we are on the same page! This office i... <span style="color:var(--blue)">more</span></p>
      <p style="font-size:9px;margin-top:18px;color:var(--muted)">26 February, 2021</p>
      <div style="display:flex;justify-content:space-between;align-items:center;margin-top:26px;border-top:1px solid #eee;padding-top:10px">
        <span style="font-size:9px;color:var(--navy)">Source:</span><b style="font-size:15px;color:var(--blue)">Searchly</b>
      </div>
    </div>
  </div>
</section>

<section class="abs commit">
  <div class="abs commit-frame"></div>
  <div class="abs commit-photo" role="img" aria-label="Photo of a smiling patient during a dental check-up"></div>
  <h2 class="abs commit-title"><span class="bold">COMMITTED TO EXCELLENCE</span><br><span class="thin">IN ORAL HEALTH CARE</span></h2>
  <div class="abs commit-rule"></div>
  <p class="abs commit-sub">Free Exam and X-Rays for New Patients</p>
  <div class="abs btn-green commit-btn">BOOK AN APPOINTMENT</div>
</section>

<footer class="abs footer">
  <div class="abs" style="left:128px;top:72px;width:260px">
    <div class="f-heading">BRIGHT HARBOR</div>
    <div class="f-rule"></div>
    <div class="f-row" style="margin-top:20px"><svg width="14" height="18" viewBox="0 0 24 30"><path fill="var(--navy)" d="M12 0C5.4 0 0 5.2 0 11.7 0 20.5 12 30 12 30s12-9.5 12-18.3C24 5.2 18.6 0 12 0zm0 16a4.5 4.5 0 110-9 4.5 4.5 0 010 9z"/></svg><span>48 Harbor View Ave., Suite A<br>Lakemont, CA 90000</span></div>
    <div class="f-row" style="margin-top:22px"><svg width="14" height="14" viewBox="0 0 24 24"><path fill="var(--navy)" d="M6.6 10.8a15.1 15.1 0 006.6 6.6l2.2-2.2c.3-.3.7-.4 1-.2 1.1.4 2.3.6 3.6.6.6 0 1 .4 1 1V20c0 .6-.4 1-1 1C10.6 21 3 13.4 3 4c0-.6.4-1 1-1h3.5c.6 0 1 .4 1 1 0 1.3.2 2.5.6 3.6.1.3 0 .7-.2 1z"/></svg><span>Call Us: (555) 014-2290</span></div>
    <div class="f-row" style="margin-top:10px"><svg width="15" height="12" viewBox="0 0 24 18"><path fill="var(--navy)" d="M0 0h24v18H0z"/><path fill="#fff" d="M1.5 1.5L12 10l10.5-8.5v2L12 12 1.5 3.5z"/></svg><span>hello@mybrightharbor.example</span></div>
    <div class="btn-red" style="width:206px;height:36px;margin-top:28px">BOOK AN APPOINTMENT</div>
  </div>
  <div class="abs" style="left:460px;top:72px;width:220px">
    <div class="f-heading">OFFICE HOURS</div>
    <div class="f-rule"></div>
    <table class="hours" style="margin-top:12px;border-collapse:collapse">
      <tr><td>Monday:</td><td>10AM–7PM</td></tr>
      <tr><td>Tuesday:</td><td>10AM–7PM</td></tr>
      <tr><td>Wednesday:</td><td>9AM–6PM</td></tr>
      <tr><td>Thursday:</td><td>9AM–6PM</td></tr>
      <tr><td>Friday:</td><td>9AM–5PM</td></tr>
      <tr><td>Saturday:</td><td>9AM–1PM</td></tr>
    </table>
  </div>
  <div class="abs" style="left:749px;top:72px">
    <div class="f-heading">OUR LOCATION</div>
    <div class="f-rule"></div>
  </div>
  <div class="abs map" role="img" aria-label="Map showing the office location on Harbor View Ave"></div>
</footer>

<div class="abs bottom-bar">
  <nav class="abs bottom-nav" style="left:0;width:1200px">
    <span style="left:131px">About Us</span>
    <span style="left:219px">Services</span>
    <span style="left:301px">Financing</span>
    <span style="left:390px">Testimonials</span>
    <span style="left:495px">New Patient Visit</span>
    <span style="left:627px">Specials</span>
    <span style="left:708px">Contact Us</span>
    <span style="left:806px">Blog</span>
  </nav>
  <div class="abs copyright">2021 Bright Harbor | All Rights Reserved</div>
  <div class="abs socials"><span></span><span></span><span></span><span></span><span></span></div>
</div>

</body>
</html>
```